Visitenkarte für Ergotherapiepraxis
Zielgruppe
Wir arbeiten mit Kindern und Erwachsene jeden Alters.
Diese Personen kommen mit Beeinträchtigungen (körperlich, seelisch, schulisch) im täglichen Leben zu uns. Wir unterstützen unsere Patienten die Beeinträchtigungen zu verringern oder zu kompensieren und so den Alltag besser bewältigen zu können.
Aufgabenstellung
Ein Design was Kinder und Erwachsene anspricht, aber nicht zu verspielt wirkt. Es soll vertrauenserweckend sein. Eventuell sollte die Visitenkarte ein "aufgehendes oder erblühendes oder aufsteigendes" Element enthalten (=zu Beginn war die Beeinträchtigung dann steigt die Lebensqualität als Folge der Behandlung)
Daten vorn:
Ergotherapiepraxis

```html
<!DOCTYPE html>
<html lang="de">
<head>
<meta charset="utf-8">
<title>Visitenkarte Ergotherapie</title>
<link rel="stylesheet" href="https://fonts.googleapis.com/css2?family=Fira+Sans+Condensed:wght@300;400;600&display=swap">
<style>
  :root {
    --page: #ececed;
    --stage: #b1b1b1;
    --card: #fffef7;
    --wine: #8b1520;
    --orange: #ec7019;
    --orange-light: #f08a40;
    --ink: #2a2a2a;
    --field: #ecebe6;
  }
  * { margin: 0; padding: 0; box-sizing: border-box; }
  html, body {
    width: 849px; height: 1200px; overflow: hidden;
    background: var(--page);
    font-family: "Fira Sans Condensed", sans-serif;
  }
  .stage {
    position: absolute; left: 0; top: 91px;
    width: 849px; height: 363px;
    background: var(--stage);
  }
  .card {
    position: absolute; top: 169px;
    width: 331px; height: 214px;
    background: var(--card);
    overflow: hidden;
  }
  .card--front { left: 53px; }
  .card--back { left: 477px; }

  .card__band {
    position: absolute; left: 0; bottom: 0;
    width: 100%; height: 42px;
    background: linear-gradient(to bottom, var(--card) 0%, var(--orange-light) 45%, var(--orange) 100%);
  }

  .brand {
    position: absolute; left: 36px; top: 60px;
    display: flex; align-items: center; gap: 7px;
    color: var(--wine); font-weight: 600; font-size: 21px; line-height: 1;
  }
  .brand__dot {
    width: 14px; height: 14px; border-radius: 50%;
    background: var(--orange);
  }

  .practice {
    position: absolute; left: 173px; top: 48px;
    font-size: 16.5px; line-height: 1; white-space: nowrap; font-weight: 400;
  }
  .practice__main { color: var(--wine); font-weight: 600; }
  .practice__sep { color: #9a8a80; font-weight: 300; margin: 0 3px; }
  .practice__sub { color: var(--orange); font-weight: 400; }
  .therapist {
    position: absolute; left: 173px; top: 77px;
    color: var(--wine); font-size: 12px; font-weight: 400; line-height: 1.2;
  }
  .address {
    position: absolute; left: 173px; top: 114px;
    color: var(--ink); font-size: 11.5px; font-weight: 300; line-height: 16px;
    font-style: normal;
  }
  .phone {
    position: absolute; left: 173px; top: 151px;
    display: flex; align-items: center; gap: 4px;
    color: var(--ink); font-size: 11.5px; font-weight: 300; line-height: 1.2;
  }

  .back__title {
    position: absolute; left: 0; width: 100%; top: 78px;
    text-align: center; color: var(--wine);
    font-size: 19px; font-weight: 600; line-height: 1.2;
  }
  .back__field {
    position: absolute; left: 60px; top: 105px;
    width: 223px; height: 40px; border-radius: 4px;
    background: var(--field);
  }
</style>
</head>
<body>
  <div class="stage"></div>

  <section class="card card--front">
    <div class="brand"><span class="brand__dot"></span>Roth</div>
    <h1 class="practice">
      <span class="practice__main">Ergotherapie</span><span class="practice__sep">|</span><span class="practice__sub">Praxis</span>
    </h1>
    <p class="therapist">Wilma Roth</p>
    <address class="address">Am Birkenweg 12<br>14979 Feldstadt, OT Ahrensau</address>
    <p class="phone">
      <svg width="9" height="9" viewBox="0 0 10 10" aria-hidden="true">
        <circle cx="5" cy="5" r="4.4" fill="none" stroke="#2a2a2a" stroke-width="0.9"/>
        <path d="M3.2 2.6c.4-.3.7 0 .9.5l.2.5c.1.3-.2.5-.3.7.3.7.8 1.2 1.5 1.5.2-.1.4-.4.7-.3l.5.2c.5.2.8.5.5.9-.4.6-1 .6-1.6.3C4.4 6.4 3.6 5.6 3.1 4.4c-.3-.7-.3-1.3.1-1.8z" fill="#2a2a2a"/>
      </svg>
      (0 33 00) 481 57
    </p>
    <div class="card__band" role="img" aria-label="Dekoratives Band in Orange und Weinrot am unteren Kartenrand"></div>
  </section>

  <section class="card card--back">
    <h2 class="back__title">Behandelnder Therapeut:</h2>
    <div class="back__field"></div>
    <div class="card__band" role="img" aria-label="Dekoratives Band in Orange und Weinrot am unteren Kartenrand"></div>
  </section>
</body>
</html>
```